Award-winnning Estate Agent needs a premium version of their 'For Sale' board design

We need a premium option for our 'For Sale' board design. We have a standard board that is attached to this brief, but were are looking to have a premium design version that we will use when selling exclusive properties. Our company name is Harbourline Vale Estates and the name for this is exclusive selection is: 'The Harbourline Collection'. The design needs to work with our current brand, but have a distinctive PREMIUM feel to it. I have uploaded the barnd guidelines and also some of the exisisting logo variations. We do NOT need a new logo but feel free to play around with colours, fonts, sizes etc. for the sign.

Target Market(s)

Property buyers & house hunters

Industry/Entity Type

Real Estate - Residential Property

Font styles to use
Sans Serif

Requirements
Must have
• A premium fee, must be square design, must be easy to read when driving past the sign
Nice to have
• I'm open ot ideas

```html
<!DOCTYPE html>
<html lang="en">
<head>
<meta charset="utf-8">
<title>Harbourline Vale Estates – For Sale Board</title>
<link rel="stylesheet" href="https://fonts.googleapis.com/css2?family=Tinos:wght@700&display=swap">
<style>
  :root {
    --board-black: #050505;
    --brand-gold: #c29f66;
    --text-white: #ffffff;
  }
  * { margin: 0; padding: 0; box-sizing: border-box; }
  html, body {
    width: 1200px;
    height: 1199px;
    overflow: hidden;
    background: var(--board-black);
  }
  .sale-board {
    position: relative;
    width: 1200px;
    height: 1199px;
    background: var(--board-black);
    font-family: "Tinos", "Times New Roman", serif;
    font-weight: 700;
    color: var(--text-white);
    text-align: center;
  }
  .collection-title {
    position: absolute;
    top: 72px;
    left: 0;
    width: 100%;
    font-size: 50px;
    letter-spacing: 0.5px;
    color: var(--brand-gold);
  }
  .sale-heading {
    position: absolute;
    top: 128px;
    left: 0;
    width: 100%;
    font-size: 156px;
    line-height: 1;
    letter-spacing: 2px;
  }
  .roof-band {
    position: absolute;
    top: 0;
    left: 0;
    width: 1200px;
    height: 1199px;
  }
  .agency-name {
    position: absolute;
    top: 640px;
    left: 0;
    width: 100%;
    font-size: 58px;
    color: var(--text-white);
  }
  .contact-phone {
    position: absolute;
    top: 920px;
    left: 0;
    width: 100%;
    display: flex;
    justify-content: center;
    align-items: center;
    gap: 28px;
    font-size: 120px;
    line-height: 1;
  }
  .phone-icon { width: 94px; height: 94px; flex: none; }
  .gold-rule {
    position: absolute;
    top: 1050px;
    left: 0;
    width: 100%;
    height: 4px;
    background: var(--brand-gold);
  }
  .web-address {
    position: absolute;
    top: 1080px;
    left: 0;
    width: 100%;
    font-size: 64px;
  }
</style>
</head>
<body>
  <main class="sale-board">
    <p class="collection-title">THE HARBOURLINE COLLECTION</p>
    <h1 class="sale-heading">FOR SALE</h1>

    <svg class="roof-band" viewBox="0 0 1200 1199" aria-hidden="true">
      <polygon points="0,510 615,330 1200,540 1200,620 615,412 0,632" fill="var(--brand-gold)"/>
    </svg>

    <p class="agency-name">Harbourline Vale Estates</p>

    <div class="contact-phone">
      <svg class="phone-icon" viewBox="0 0 100 100" aria-hidden="true">
        <circle cx="50" cy="50" r="50" fill="var(--brand-gold)"/>
        <path d="M36 26c3-2 6-1 7 2l4 9c1 2 0 4-2 6l-3 3c2 6 7 11 13 13l3-3c2-2 4-3 6-2l9 4c3 1 4 4 2 7l-3 5c-2 3-6 4-10 3-17-5-30-18-35-35-1-4 0-8 3-10z" fill="var(--board-black)"/>
      </svg>
      <span class="phone-number">01632 960417</span>
    </div>

    <div class="gold-rule"></div>
    <p class="web-address">harbourlinevaleestates.co.uk</p>
  </main>
</body>
</html>
```